Velora Entertainment

Logo for business card design

Target Market(s)

potential film investors and screenwriters

Industry/Entity Type

Business

Contact Information for Business Card

as shown, website here is a placeholder position

Requirements
Must have
• great visual appeal
Nice to have
• harmony of colors; must evoke spirit of
• U.S.-China cooperation

```html
<!DOCTYPE html>
<html lang="en">
<head>
<meta charset="utf-8">
<title>Velora Entertainment — Business Card</title>
<link href="https://fonts.googleapis.com/css2?family=Source+Sans+3:wght@400;600;700&display=swap" rel="stylesheet">
<style>
  :root {
    --backdrop: #e4e4e4;
    --card-white: #f4f4f4;
    --card-grey: #828385;
    --brand-red: #cc1f24;
    --brand-yellow: #e3bb13;
    --brand-navy: #1d1f7a;
    --ink: #1b1b1b;
    --divider: #b9b9b9;
  }
  * { margin: 0; padding: 0; box-sizing: border-box; }
  html, body {
    width: 1105px;
    height: 1200px;
    overflow: hidden;
    background: var(--backdrop);
    font-family: "Source Sans 3", "Helvetica Neue", Arial, sans-serif;
  }
  .card {
    position: absolute;
    left: 182px;
    width: 746px;
    height: 425px;
  }
  .card--front { top: 120px; background: var(--card-white); }
  .card--back { top: 637px; background: var(--card-grey); }

  .brand {
    position: absolute;
    display: flex;
    align-items: center;
    gap: 12px;
    font-weight: 700;
    font-size: 29px;
    letter-spacing: 0.5px;
    white-space: nowrap;
  }
  .brand__mark { width: 22px; height: 22px; background: var(--brand-red); flex: none; }
  .card--front .brand { left: 58px; top: 164px; color: var(--brand-navy); }
  .card--back .brand {
    left: 50%; top: 50%;
    transform: translate(-50%, -50%);
    color: #ffffff;
  }
  .card--back .brand__mark { background: #ffffff; }

  .divider {
    position: absolute;
    left: 388px;
    top: 84px;
    width: 1px;
    height: 249px;
    background: var(--divider);
  }
  .contact {
    position: absolute;
    left: 427px;
    top: 72px;
    color: var(--ink);
    font-size: 19px;
    line-height: 1.45;
  }
  .contact__name { color: var(--brand-red); font-size: 27px; font-weight: 600; line-height: 1.2; }
  .contact__role { color: var(--brand-navy); font-size: 20px; line-height: 1.3; }
  .contact__address { margin-top: 22px; margin-bottom: 12px; }
  .contact__line { display: flex; align-items: center; gap: 12px; }
  .contact__icon { width: 17px; height: 17px; flex: none; fill: var(--brand-red); }

  .stripes {
    position: absolute;
    left: 0; right: 0;
    top: 392px;
    height: 4px;
    display: flex;
  }
  .stripes span { flex: 1; }
  .stripes .red { background: var(--brand-red); }
  .stripes .yellow { background: var(--brand-yellow); }
  .stripes .navy { background: var(--brand-navy); }
</style>
</head>
<body>
  <section class="card card--front" aria-label="Card front">
    <div class="brand"><span class="brand__mark"></span>Velora Entertainment</div>
    <div class="divider"></div>
    <div class="contact">
      <div class="contact__name">Evan Marlow</div>
      <div class="contact__role">CEO/Founder</div>
      <div class="contact__address">4120 Cedar Hollow Road<br>Juneau, Alaska 99801</div>
      <div class="contact__line">
        <svg class="contact__icon" viewBox="0 0 24 24" aria-hidden="true"><path d="M6.6 10.8a15.1 15.1 0 0 0 6.6 6.6l2.2-2.2c.3-.3.7-.4 1-.2 1.1.4 2.3.6 3.6.6.6 0 1 .4 1 1V20c0 .6-.4 1-1 1A17 17 0 0 1 3 4c0-.6.4-1 1-1h3.5c.6 0 1 .4 1 1 0 1.3.2 2.5.6 3.6.1.3 0 .7-.2 1z"/></svg>
        <span>555 214 7086</span>
      </div>
      <div class="contact__line">
        <svg class="contact__icon" viewBox="0 0 24 24" aria-hidden="true"><path d="M7 1h10a2 2 0 0 1 2 2v18a2 2 0 0 1-2 2H7a2 2 0 0 1-2-2V3a2 2 0 0 1 2-2zm0 3v14h10V4zm5 15.2a1.2 1.2 0 1 0 0 2.4 1.2 1.2 0 0 0 0-2.4z"/></svg>
        <span>555 390 1427</span>
      </div>
      <div class="contact__line">
        <svg class="contact__icon" viewBox="0 0 24 24" aria-hidden="true"><path d="M2 5h20v14H2zm2 2v.5l8 5.5 8-5.5V7zm0 3v7h16v-7l-8 5.5z"/></svg>
        <span>hello@velora-ent.com</span>
      </div>
      <div class="contact__line">
        <svg class="contact__icon" viewBox="0 0 24 24" aria-hidden="true"><path d="M12 2a10 10 0 1 0 0 20 10 10 0 0 0 0-20zm-1 17.9A8 8 0 0 1 4.2 10.6L9 15.4v1a2 2 0 0 0 2 2zm6.9-2.5A2 2 0 0 0 16 16h-1v-3a1 1 0 0 0-1-1H8v-2h2a1 1 0 0 0 1-1V7h2a2 2 0 0 0 2-2v-.4a8 8 0 0 1 2.9 12.8z"/></svg>
        <span>www.velora-ent.com</span>
      </div>
    </div>
    <div class="stripes"><span class="red"></span><span class="yellow"></span><span class="navy"></span></div>
  </section>

  <section class="card card--back" aria-label="Card back">
    <div class="brand"><span class="brand__mark"></span>Velora Entertainment</div>
  </section>
</body>
</html>
```